Business Card - Business Consultancy

Newly Established Company, specializing in Business Consultancy, Human Resource Management, Talent Acquisition and Payroll Solutions.

We need a Business card design which portrays "elegance" and a very sleek yet business-like design. We would like a nice blue trimming (which goes well with the logo) to separate the content of the business card at the top. We would also like to see the design using the color silver either as a background or incorporated into it.

The final design should be a Business card which has colors matching the logo; a nice font; the above-mentioned specifics that adheres to the theme of "a stylish and professional business"

FYI: please do not have too fanciful designs.

Industry/Entity Type

Business Consultant

Contact Information for Business Card

Darren Lim
Business Development Director
Arbor Talent Consulting Private Limited
27 Wexley Street, #05-03B
Harbourgate Trade Building
Singapore 059317
Mobile : (+65) 98354417
Email : dlim@arbortalent-advisory.com
Alternative : arbortalentadvisory@mailbox-example.com

Requirements
Must have
• Nice Blue Trimming matching Logo which separates content, see attached
• Design incorporates either a silver background or the use of the color silver
Should not have
• No Fanciful Designs
• No Childish Designs
• No Overly Complicated Designs

```html
<!DOCTYPE html>
<html lang="en">
<head>
<meta charset="utf-8">
<title>Arbor Talent Consulting – Business Card</title>
<link href="https://fonts.googleapis.com/css2?family=Open+Sans:wght@400;600;700&display=swap" rel="stylesheet">
<style>
  :root {
    --backdrop-top: #dfe2e5;
    --backdrop-bottom: #c9cdd1;
    --card: #ffffff;
    --card-edge: #cfd3d7;
    --silver: #b8bdc2;
    --silver-light: #e3e6e9;
    --brand-blue: #1a86c8;
    --brand-green: #7cbd2b;
    --ink: #3a3a3a;
    --ink-soft: #6b6b6b;
  }
  * { box-sizing: border-box; margin: 0; padding: 0; }
  html, body {
    width: 1200px;
    height: 864px;
    overflow: hidden;
    font-family: "Open Sans", Arial, sans-serif;
  }
  body {
    background: linear-gradient(160deg, var(--backdrop-top), var(--backdrop-bottom));
  }
  .stage {
    position: relative;
    width: 1200px;
    height: 864px;
  }
  .card {
    position: absolute;
    width: 600px;
    height: 340px;
    background: var(--card);
    border: 1px solid var(--card-edge);
    box-shadow: 0 6px 18px rgba(0,0,0,0.14);
    overflow: hidden;
  }
  .card--front { left: 300px; top: 70px; }
  .card--back  { left: 300px; top: 450px; }

  /* blue trim with silver hairline across the top of each card */
  .card__trim {
    position: absolute;
    left: 0;
    top: 0;
    width: 100%;
    height: 8px;
    background: var(--brand-blue);
    border-bottom: 3px solid var(--silver);
  }
  /* silver base band */
  .card__base {
    position: absolute;
    left: 0;
    bottom: 0;
    width: 100%;
    height: 10px;
    background: linear-gradient(90deg, var(--silver-light), var(--silver), var(--silver-light));
  }

  /* brand wordmark */
  .brand {
    display: flex;
    align-items: center;
    gap: 12px;
  }
  .brand__dot {
    width: 46px;
    height: 46px;
    border-radius: 50%;
    background: var(--brand-blue);
    flex: none;
  }
  .brand__name {
    font-weight: 700;
    color: var(--ink);
    line-height: 1.1;
  }

  /* front */
  .card--front .brand {
    position: absolute;
    left: 130px;
    top: 118px;
  }
  .card--front .brand__name { font-size: 26px; }
  .front__tagline {
    position: absolute;
    left: 188px;
    top: 170px;
    font-size: 11px;
    font-weight: 700;
    color: var(--ink-soft);
    letter-spacing: 0.3px;
  }

  /* back */
  .card--back .brand {
    position: absolute;
    right: 34px;
    top: 38px;
  }
  .card--back .brand__dot { width: 56px; height: 56px; }
  .card--back .brand__name { font-size: 22px; width: 150px; }

  .person {
    position: absolute;
    left: 60px;
    top: 50px;
  }
  .person__name {
    font-size: 19px;
    font-weight: 600;
    color: var(--brand-blue);
    letter-spacing: 0.5px;
  }
  .person__title {
    font-size: 14px;
    color: var(--brand-green);
    margin-top: 2px;
  }
  .company {
    position: absolute;
    left: 60px;
    top: 118px;
  }
  .company__name {
    font-size: 14px;
    font-weight: 700;
    color: var(--brand-blue);
    letter-spacing: 0.3px;
  }
  .company__address {
    font-style: normal;
    font-size: 14px;
    line-height: 17px;
    color: var(--ink);
    margin-top: 4px;
  }
  .contact {
    position: absolute;
    left: 48px;
    top: 228px;
    list-style: none;
    font-size: 14px;
    line-height: 22px;
    color: var(--ink);
  }
  .contact__item {
    display: flex;
    align-items: center;
    gap: 8px;
  }
  .contact__icon {
    width: 11px;
    height: 11px;
    flex: none;
    fill: var(--brand-blue);
  }
</style>
</head>
<body>
<main class="stage">

  <section class="card card--front" aria-label="Card front">
    <span class="card__trim"></span>
    <div class="brand">
      <span class="brand__dot"></span>
      <span class="brand__name">Arbor Talent Consulting</span>
    </div>
    <p class="front__tagline">Recruitment &nbsp;I&nbsp; HR Solutions I Business Consultancy</p>
    <span class="card__base"></span>
  </section>

  <section class="card card--back" aria-label="Card back">
    <span class="card__trim"></span>
    <div class="brand">
      <span class="brand__dot"></span>
      <span class="brand__name">Arbor Talent Consulting</span>
    </div>

    <div class="person">
      <h1 class="person__name">DARREN LIM</h1>
      <p class="person__title">Business Development Director</p>
    </div>

    <div class="company">
      <h2 class="company__name">ARBOR TALENT CONSULTING PRIVATE LIMITED</h2>
      <address class="company__address">
        27 Wexley Street, #05-03B<br>
        Harbourgate Trade Building<br>
        Singapore 059317
      </address>
    </div>

    <ul class="contact">
      <li class="contact__item">
        <svg class="contact__icon" viewBox="0 0 12 12" aria-hidden="true">
          <path d="M1 4 Q6 0 11 4 L9 5.5 L8 4.5 Q6 4 4 4.5 L3 5.5 Z M3 6 H9 L10 11 H2 Z"/>
        </svg>
        (+65) 98354417
      </li>
      <li class="contact__item">
        <svg class="contact__icon" viewBox="0 0 12 12" aria-hidden="true">
          <path d="M0 2 H12 V10 H0 Z"/><path d="M0.5 2.5 L6 7 L11.5 2.5" stroke="#fff" stroke-width="1" fill="none"/>
        </svg>
        Email : dlim@arbortalent-advisory.com
      </li>
      <li class="contact__item">
        <svg class="contact__icon" viewBox="0 0 12 12" aria-hidden="true">
          <path d="M0 2 H12 V10 H0 Z"/><path d="M0.5 2.5 L6 7 L11.5 2.5" stroke="#fff" stroke-width="1" fill="none"/>
        </svg>
        Email : arbortalentadvisory@mailbox-example.com
      </li>
    </ul>
    <span class="card__base"></span>
  </section>

</main>
</body>
</html>
```